Meridale Nutrition needs Stationary and a business card

We would like to use our current logo. The text can be moved around as needed. The stationary needs to be a 'first page' where the logo is more prominent to be impressive on higher quality paper and a second page where the logo is more subtle where there will be much more information on the page. There are 2 clinic locations which will need include name, address, phone number, fax number, web address. The business card should be single sided and contain this information also.
The design must be contemporary and sophisticated as this is a science based diet run out of a medical clinic.

Target Market(s)

People wanting to lose weight, athletes looking to optimise performance, people with arthritis or fighting cancer

Industry/Entity Type

Business

Contact Information for Business Card

must use the logo. I have attached an example card with the practice details on it. there must be space for the doctors name. Also the website www.meridalenutrition.com.au

Requirements
Must have
• the logo, the business adresses and phone numbers, the website, the doctors name and qualifications
Nice to have
• some creativity
Should not have
• Do not simply reproduce the existing card please

```html
<!DOCTYPE html>
<html lang="en">
<head>
<meta charset="utf-8">
<title>Meridale Nutrition — Business Card</title>
<link rel="stylesheet" href="https://fonts.googleapis.com/css2?family=Arimo:wght@400;700&display=swap">
<style>
  :root {
    --backdrop: #e6e7ea;
    --card: #ffffff;
    --card-shade: #eef0f2;
    --band: #22b3e6;
    --band-light: #5cc9ef;
    --navy: #1d3566;
    --text: #5a5d62;
    --tel: #2a6fc0;
    --rule: #c9ccd1;
  }
  * { box-sizing: border-box; margin: 0; padding: 0; }
  html, body {
    width: 1200px; height: 950px; overflow: hidden;
    background: var(--backdrop);
    font-family: "Arimo", Arial, sans-serif;
  }
  .card {
    position: absolute; left: 250px;
    width: 700px; height: 420px;
    background: linear-gradient(180deg, var(--card) 0%, var(--card) 55%, var(--card-shade) 100%);
    box-shadow: 0 8px 24px rgba(0,0,0,0.12);
    overflow: hidden;
  }
  .card-back { top: 40px; }
  .card-front { top: 490px; }

  /* Back side */
  .back-brand {
    position: absolute; inset: 0;
    display: flex; align-items: center; justify-content: center; gap: 28px;
  }
  .back-dot { width: 190px; height: 190px; border-radius: 50%; background: var(--band); }
  .back-name {
    font-weight: 700; font-size: 38px; line-height: 1.08;
    color: var(--navy); text-transform: uppercase; letter-spacing: 1px;
  }

  /* Front side */
  .brand {
    position: absolute; left: 50px; top: 42px;
    display: flex; align-items: center; gap: 16px;
  }
  .brand-dot { width: 88px; height: 88px; border-radius: 50%; background: var(--band); }
  .brand-name {
    font-weight: 700; font-size: 26px; line-height: 1.08;
    color: var(--navy); text-transform: uppercase; letter-spacing: 1px;
  }
  .site {
    position: absolute; right: 40px; top: 140px;
    font-size: 15px; font-weight: 700; color: var(--navy);
  }
  .name-band {
    position: absolute; left: 0; top: 172px; width: 100%; height: 68px;
    background: var(--band);
    padding: 10px 50px 0;
  }
  .doctor-name { font-size: 24px; font-weight: 400; color: var(--navy); }
  .credentials { font-size: 13px; margin-top: 6px; color: var(--navy); }
  .band-rule {
    position: absolute; left: 0; top: 240px; width: 100%; height: 3px;
    background: var(--rule);
  }
  .details {
    position: absolute; left: 50px; top: 258px; right: 30px;
    display: grid; grid-template-columns: 195px 215px 1fr; column-gap: 14px;
    font-size: 14.5px; line-height: 1.32; color: var(--text);
  }
  .clinic { font-style: normal; }
  .clinic-offset { padding-top: 20px; }
  .clinic-name { font-weight: 700; color: var(--navy); }
  .label { font-weight: 700; color: var(--tel); }
  .specialties { padding-top: 40px; }
  .accent-strip {
    position: absolute; right: 0; bottom: 0; width: 266px; height: 10px;
    background: var(--band-light);
  }
</style>
</head>
<body>
  <section class="card card-back" aria-label="Card back">
    <div class="back-brand">
      <span class="back-dot"></span>
      <span class="back-name">Meridale<br>Nutrition</span>
    </div>
  </section>

  <main class="card card-front">
    <header class="brand">
      <span class="brand-dot"></span>
      <span class="brand-name">Meridale<br>Nutrition</span>
    </header>
    <p class="site">www.meridalenutrition.com.au</p>

    <section class="name-band">
      <h1 class="doctor-name">Dr Elliot Marsh</h1>
      <p class="credentials">MBBS (NSW) MBiomedE FRACS (Ortho) FAOrthA Orthopaedic Surgeon</p>
    </section>
    <div class="band-rule"></div>

    <section class="details">
      <address class="clinic">
        <div class="clinic-name">Harlow</div>
        <div>22 Kestrel Street</div>
        <div>Harlow NSW 2090</div>
        <div><span class="label">Tel:</span> 02 9000 4821</div>
        <div><span class="label">Fax:</span> 02 9000 4822</div>
      </address>
      <address class="clinic clinic-offset">
        <div class="clinic-name">Ashgrove</div>
        <div>15-17 Linden Road</div>
        <div>Ashgrove NSW 2145</div>
        <div><span class="label">Tel:</span> 02 9000 7364</div>
        <div><span class="label">Fax:</span> 02 9000 7365</div>
      </address>
      <div class="specialties">
        <div>Shoulder and Elbow</div>
        <div>www.elliotmarsh.com.au</div>
        <div>Knee surgery</div>
        <div>www.jointclinic.com.au</div>
      </div>
    </section>
    <div class="accent-strip"></div>
  </main>
</body>
</html>
```